Template Flyer- Corewell Stretch & Flow

I am wanting a template 1 page flyer designed to use on the back ground of newsletter (faded background) and for our advertising posters in A4, A3, for Facebook and Instagram compatibility.

I have loaded an example from another Studio called Pinegrove (file 3)- each time they have a new workshop to advertise a picture is placed in the little circle (so this is something I would want to do too where I can load a new picture each time a new workshop is running)- They have used the flyer like a water mark...I like this.

Our colour palette is what is on our logos and you can also visit our website for a feel for what we like www.corewellstretch.com.au

I need some of the designs edited a bit more and because of the time difference, there seems to be a 24hour period where we communicate with each other. May I please request another 2 days extension

Requirements
Must have
• Id like to have a picture in the back ground. My favourite back ground that has been produced so far is a background of both picture file 9 and 10 in either.
Nice to have
• 3 picture circles options to advertise the events/workshops I have each year.
• Brush stroke style circles (see picture attached)rather then smooth circles for the picture area (in a grey tone)
Should not have
• No BLACK colour writing or black circles

```html
<!DOCTYPE html>
<html lang="en">
<head>
<meta charset="utf-8">
<title>Corewell Stretch &amp; Flow – Workshop Flyer</title>
<link href="https://fonts.googleapis.com/css2?family=Roboto+Condensed:wght@300;400;700&family=Roboto:wght@400&display=swap" rel="stylesheet">
<style>
  :root{
    --teal:#1ea3bf;
    --grey-ink:#4a4f53;
    --grey-soft:#8f9598;
    --ring:#c9c4be;
    --stage:#f2f2f2;
    --white:#ffffff;
    --photo-deep:#a9aeb1;
    --photo-mid:#c4c8ca;
    --photo-light:#e3e5e6;
    --photo-pale:#eceeee;
  }
  *{box-sizing:border-box;margin:0;padding:0}
  html,body{width:768px;height:1200px;overflow:hidden;background:var(--stage)}
  .flyer{
    position:absolute;left:24px;top:90px;width:720px;height:1020px;overflow:hidden;
    background:var(--photo-pale);
    box-shadow:0 2px 10px rgba(0,0,0,.12);
    font-family:"Roboto Condensed",sans-serif;
  }
  .flyer__backdrop-photo{
    position:absolute;inset:0;
    background:linear-gradient(170deg,
      var(--photo-deep) 0%,
      var(--photo-mid) 22%,
      var(--photo-light) 48%,
      var(--photo-mid) 70%,
      var(--photo-light) 88%,
      var(--photo-pale) 100%);
  }
  .flyer__kicker{
    position:absolute;top:36px;left:0;width:100%;text-align:center;
    font-weight:400;font-size:33px;color:var(--grey-ink);letter-spacing:-.3px;
  }
  .flyer__headline{
    position:absolute;top:82px;left:0;width:100%;text-align:center;
    font-weight:700;font-size:80px;line-height:1;color:var(--teal);letter-spacing:-1px;
  }
  .photo-circles{position:absolute;left:0;top:0}
  .info-row{position:absolute;display:flex;height:37px;font-size:22px}
  .info-row__label{
    background:var(--teal);color:var(--white);font-weight:400;
    display:flex;align-items:center;justify-content:center;
  }
  .info-row__value{
    background:var(--white);color:var(--grey-ink);border:1px solid #c8cbcc;
    font-family:"Roboto",sans-serif;font-size:19px;
    display:flex;align-items:center;padding-left:12px;
  }
  .info-row--date{left:65px;top:666px}
  .info-row--date .info-row__label{width:67px}
  .info-row--date .info-row__value{width:236px}
  .info-row--time{left:387px;top:666px}
  .info-row--time .info-row__label{width:68px}
  .info-row--time .info-row__value{width:202px}
  .info-row--location{left:99px;top:718px}
  .info-row--location .info-row__label{width:120px}
  .info-row--location .info-row__value{width:401px}
  .info-row--cost{left:249px;top:770px}
  .info-row--cost .info-row__label{width:120px}
  .info-row--cost .info-row__value{width:101px}
  .workshop{position:absolute;left:35px;top:840px;width:282px}
  .workshop__title{font-size:27px;font-weight:400;color:var(--teal);margin-bottom:12px}
  .workshop__text{
    font-family:"Roboto",sans-serif;font-size:9.5px;line-height:13px;color:var(--grey-ink);
    text-align:justify;margin-bottom:13px;
  }
  .brand{
    position:absolute;left:400px;top:878px;display:flex;align-items:center;gap:10px;
  }
  .brand__dot{width:38px;height:38px;border-radius:50%;border:2px solid var(--grey-soft)}
  .brand__name{font-weight:300;font-size:27px;color:var(--grey-soft)}
  .web-bar{
    position:absolute;left:369px;top:967px;width:351px;height:41px;
    background:var(--teal);border-radius:14px 0 0 14px;
    display:flex;align-items:center;justify-content:center;
    font-family:"Roboto",sans-serif;font-size:20px;color:var(--white);
  }
</style>
</head>
<body>
  <main class="flyer">
    <div class="flyer__backdrop-photo" role="img" aria-label="Faded full-page grey photograph of the studio entrance with a picket fence, used as a watermark background"></div>

    <p class="flyer__kicker">PILATES AND YOGA FOR YOUR</p>
    <h1 class="flyer__headline">MIND, BODY &amp; SOUL</h1>

    <svg class="photo-circles" width="720" height="1020" viewBox="0 0 720 1020">
      <defs>
        <linearGradient id="studioTones" x1="0" y1="0" x2="1" y2="1">
          <stop offset="0" stop-color="#e9eaea"/>
          <stop offset=".45" stop-color="#b9bcbd"/>
          <stop offset=".8" stop-color="#6f7476"/>
          <stop offset="1" stop-color="#9a9d9e"/>
        </linearGradient>
        <linearGradient id="detailTones" x1="0" y1="0" x2="1" y2="0">
          <stop offset="0" stop-color="#8a817a"/>
          <stop offset=".5" stop-color="#d6d2cd"/>
          <stop offset="1" stop-color="#a49c95"/>
        </linearGradient>
      </defs>
      <circle class="ring-main" cx="357" cy="393" r="207" fill="none" stroke="var(--ring)" stroke-width="7"/>
      <path class="ring-accent" d="M 150 393 A 207 207 0 0 0 428 588" fill="none" stroke="var(--teal)" stroke-width="7"/>
      <circle cx="357" cy="393" r="203" fill="url(#studioTones)" role="img" aria-label="Photo of a studio floor with rows of mats, blocks and bolsters"/>
      <circle class="ring-small" cx="170" cy="541" r="112" fill="var(--ring)"/>
      <circle cx="170" cy="541" r="106" fill="url(#detailTones)" role="img" aria-label="Photo of hanging tassel decorations by a wall"/>
    </svg>

    <div class="info-row info-row--date"><span class="info-row__label">DATE</span><span class="info-row__value">SUNDAY, XX-XX-2018</span></div>
    <div class="info-row info-row--time"><span class="info-row__label">TIME</span><span class="info-row__value">XX am to XX pm</span></div>
    <div class="info-row info-row--location"><span class="info-row__label">LOCATION</span><span class="info-row__value">LOREM IPSUM IS SIMPLY DUMMY TEXT</span></div>
    <div class="info-row info-row--cost"><span class="info-row__label">COST</span><span class="info-row__value">$XX</span></div>

    <section class="workshop">
      <h2 class="workshop__title">OUR WORKSHOP</h2>
      <p class="workshop__text">Lorem Ipsum is simply dummy text of the printing and typesetting industry. Lorem Ipsum has been the industry's standard dummy text ever since the 1500s, when an unknown printer took a galley of type and scrambled it to make a type specimen book.</p>
      <p class="workshop__text">Lorem Ipsum is simply dummy text of the printing and typesetting industry. Lorem Ipsum has been the industry's standard dummy text.</p>
    </section>

    <div class="brand">
      <span class="brand__dot"></span>
      <span class="brand__name">Corewell Stretch &amp; Flow</span>
    </div>

    <div class="web-bar">www.corewellstretch.com.au</div>
  </main>
</body>
</html>
```